Mobile Fitness snd Therapy Business Card Design

I need a business card designed for my mobile fitness and therapy business.

Please view the images that I have uploaded. I like the simplicity of the design that I have attached. I adapted it with my information

Target Market(s)

Those seeking personal training, injury rehabilitation or massage therapy.

Industry/Entity Type

Business

Contact Information for Business Card

Derek Fulham - MSc, CAT(C), RMT, CSCS, Pn2
e-mail: derek@vantrelo.com
website: www.vantrelo.com
instagram: @derek_fulham

Font styles to use
Sans Serif

Colors
3176b5
0355a3

Requirements
Must have
• "Contact us to receive a FREE assessment"
• Services offered:
• Personal Training
• Golf Fitness
• Injury Rehab
• Massage Therapy
• Yoga
Nice to have
• Consistent colours with brand
• - Dark Blue: #232837
• - Blue: #5096f0
• Consistent look/feel with the website: www.vantrelo.com

```html
<!DOCTYPE html>
<html lang="en">
<head>
<meta charset="utf-8">
<title>Vantrelo Business Card</title>
<link rel="stylesheet" href="https://fonts.googleapis.com/css2?family=Montserrat:wght@600;700&family=Open+Sans:wght@400;600&display=swap">
<style>
  :root {
    --card-navy: #232837;
    --accent-blue: #5096f0;
    --brand-blue: #3176b5;
    --text-white: #ffffff;
    --page-bg: #e4e2de;
  }
  * { margin: 0; padding: 0; box-sizing: border-box; }
  html, body { width: 1200px; height: 1000px; overflow: hidden; }
  body {
    background: var(--page-bg);
    position: relative;
    font-family: "Open Sans", Arial, sans-serif;
    color: var(--text-white);
  }
  .card {
    position: absolute;
    left: 266px;
    width: 666px;
    height: 397px;
    background: var(--card-navy);
  }
  .card--front { top: 74px; }
  .card--back { top: 533px; }

  .edge-bar {
    position: absolute;
    top: 129px;
    width: 10px;
    height: 139px;
    background: var(--text-white);
  }
  .edge-bar--left { left: 0; }
  .edge-bar--right { right: 0; }

  .column-divider {
    position: absolute;
    left: 332px;
    top: 129px;
    width: 2px;
    height: 139px;
    background: var(--text-white);
  }

  .person-name {
    position: absolute;
    left: 67px;
    top: 127px;
    font-family: "Montserrat", Arial, sans-serif;
    font-weight: 700;
    font-size: 20px;
    letter-spacing: 0.2px;
  }
  .person-credentials {
    position: absolute;
    left: 67px;
    top: 154px;
    font-size: 15px;
    color: var(--accent-blue);
  }
  .contact-list { list-style: none; }
  .contact-item {
    position: absolute;
    left: 67px;
    display: flex;
    align-items: center;
    gap: 7px;
    font-size: 17px;
    line-height: 1;
  }
  .contact-item svg { width: 16px; height: 16px; flex: none; }
  .contact-item--social { top: 197px; }
  .contact-item--email { top: 224px; }
  .contact-item--web { top: 247px; }

  .service-list { list-style: none; }
  .service-item {
    position: absolute;
    left: 401px;
    display: flex;
    align-items: center;
    gap: 8px;
    font-size: 17.5px;
    line-height: 1;
  }
  .service-marker {
    width: 9px;
    height: 9px;
    background: var(--accent-blue);
    flex: none;
  }

  .offer-line {
    position: absolute;
    left: 0;
    width: 100%;
    top: 349px;
    text-align: center;
    font-size: 17px;
  }

  .brand-name {
    position: absolute;
    left: 0;
    width: 100%;
    top: 152px;
    text-align: center;
    font-family: "Montserrat", Arial, sans-serif;
    font-weight: 600;
    font-size: 56px;
    letter-spacing: 5px;
    line-height: 1;
  }
  .brand-tagline {
    position: absolute;
    left: 0;
    width: 100%;
    top: 222px;
    text-align: center;
    font-family: "Montserrat", Arial, sans-serif;
    font-weight: 700;
    font-size: 18px;
    letter-spacing: 2.6px;
  }
</style>
</head>
<body>
  <section class="card card--front">
    <span class="edge-bar edge-bar--left"></span>
    <span class="edge-bar edge-bar--right"></span>

    <h1 class="person-name">DEREK FULHAM</h1>
    <p class="person-credentials">MSc, CAT(C), RMT, CSCS, Pn2</p>

    <ul class="contact-list">
      <li class="contact-item contact-item--social">
        <svg viewBox="0 0 16 16"><rect x="1" y="1" width="14" height="14" fill="none" stroke="#fff" stroke-width="2"/></svg>
        @derek_fulham
      </li>
      <li class="contact-item contact-item--email">
        <svg viewBox="0 0 16 16"><rect x="1" y="3" width="14" height="10" fill="#fff"/><path d="M1 3l7 6 7-6" fill="none" stroke="#232837" stroke-width="1.4"/></svg>
        derek@vantrelo.com
      </li>
      <li class="contact-item contact-item--web">
        <svg viewBox="0 0 16 16"><circle cx="8" cy="8" r="6.5" fill="none" stroke="#fff" stroke-width="1.6"/><path d="M1.5 8h13M8 1.5c-3 3.5-3 9.5 0 13M8 1.5c3 3.5 3 9.5 0 13" fill="none" stroke="#fff" stroke-width="1.2"/></svg>
        www.vantrelo.com
      </li>
    </ul>

    <span class="column-divider"></span>

    <ul class="service-list">
      <li class="service-item" style="top:129px"><span class="service-marker"></span>Personal Training</li>
      <li class="service-item" style="top:159px"><span class="service-marker"></span>Golf Fitness</li>
      <li class="service-item" style="top:190px"><span class="service-marker"></span>Injury Rehab</li>
      <li class="service-item" style="top:220px"><span class="service-marker"></span>Massage Therapy</li>
      <li class="service-item" style="top:251px"><span class="service-marker"></span>Yoga</li>
    </ul>

    <p class="offer-line">Contact us to receive a FREE assessment</p>
  </section>

  <section class="card card--back">
    <h2 class="brand-name">VANTRELO</h2>
    <p class="brand-tagline">NUTRITION - FITNESS - HEALTH</p>
  </section>
</body>
</html>
```